Personal Injury Lawyer Billboard

I would like a design created featuring the image of the lawyer centered in the middle of the design.
To the left of the lawyer's image it should read "INJURED?"
To the right of the lawyer's image, it should read "CALL DEAN!"
Under Call Dean, include the phone number 318-555-0187.
At the bottom of the design include the lawyers information "Dean Marlowe Accident & Injury Lawyers"
PLEASE REMOVED THE BACKGROUND IMAGERY OF THE PHOTO SUBMITTED. Also, the colors for this design should match the colors shown in the logo (navy, white and relective soft gold). Please use those color combinations in ways that best stand out.

```html
<!DOCTYPE html>
<html lang="en">
<head>
<meta charset="utf-8">
<title>Dean Marlowe Accident &amp; Injury Lawyers Billboard</title>
<link href="https://fonts.googleapis.com/css2?family=Cormorant+Garamond:wght@600;700&family=Libre+Baskerville&family=Roboto+Condensed:wght@400;700&display=swap" rel="stylesheet">
<style>
  :root {
    --page: #ffffff;
    --red: #c01f2f;
    --red-orange: #e8412c;
    --orange: #f15a29;
    --amber: #f7941d;
    --navy-top: #2b3a8f;
    --navy-bottom: #0f1f4f;
    --gold: #f5c518;
    --white: #ffffff;
    --suit: #1c2a66;
  }
  html, body {
    margin: 0;
    width: 1200px;
    height: 1105px;
    overflow: hidden;
    background: var(--page);
  }
  .billboard {
    position: absolute;
    left: 40px;
    top: 389px;
    width: 1120px;
    height: 327px;
    display: block;
  }
  .headline {
    font-family: "Cormorant Garamond", Georgia, serif;
    font-weight: 700;
    font-size: 96px;
    fill: var(--white);
  }
  .services {
    font-family: "Roboto Condensed", "Arial Narrow", sans-serif;
    font-weight: 400;
    font-size: 18px;
    fill: var(--white);
  }
  .call-out {
    font-family: "Cormorant Garamond", Georgia, serif;
    font-weight: 700;
    font-size: 46px;
    fill: var(--gold);
  }
  .phone {
    font-family: "Libre Baskerville", Georgia, serif;
    font-size: 44px;
    letter-spacing: 1px;
    fill: var(--white);
  }
  .firm-name {
    font-family: "Roboto Condensed", "Arial Narrow", sans-serif;
    font-weight: 700;
    font-size: 40px;
    fill: var(--white);
  }
  .firm-tagline {
    font-family: "Roboto Condensed", "Arial Narrow", sans-serif;
    font-weight: 700;
    font-size: 20px;
    fill: var(--white);
  }
</style>
</head>
<body>
<svg class="billboard" viewBox="0 0 1120 327" xmlns="http://www.w3.org/2000/svg" aria-label="Dean Marlowe Accident and Injury Lawyers billboard">
  <defs>
    <linearGradient id="navy-field" x1="0" y1="0" x2="0" y2="1">
      <stop offset="0" stop-color="var(--navy-top)"/>
      <stop offset="1" stop-color="var(--navy-bottom)"/>
    </linearGradient>
    <linearGradient id="portrait-tone" x1="0" y1="0" x2="0" y2="1">
      <stop offset="0" stop-color="#3a2c28" stop-opacity="0.9"/>
      <stop offset="0.35" stop-color="#2a3270"/>
      <stop offset="1" stop-color="var(--suit)"/>
    </linearGradient>
  </defs>

  <rect class="red-field" x="0" y="0" width="1120" height="327" fill="var(--red)"/>
  <polygon class="stripe stripe-red-orange" points="416,0 452,0 606,327 570,327" fill="var(--red-orange)"/>
  <polygon class="stripe stripe-orange" points="452,0 488,0 642,327 606,327" fill="var(--orange)"/>
  <polygon class="stripe stripe-amber" points="488,0 525,0 679,327 642,327" fill="var(--amber)"/>
  <polygon class="navy-field" points="525,0 1120,0 1120,327 679,327" fill="url(#navy-field)"/>

  <rect class="portrait" x="481" y="4" width="254" height="323" rx="0" fill="url(#portrait-tone)" role="img" aria-label="Portrait of the lawyer in a navy suit and green tie, smiling with a raised fist"/>

  <text class="headline" x="107" y="165">Injured?</text>

  <text class="services" x="43" y="258">• Personal Injury • Social Security Disability • Criminal Defense • Domestic Relations</text>
  <text class="services" x="110" y="288">• Wills and Estates • Appeals • Contract Dispute • Civil Litigation</text>

  <text class="call-out" x="906" y="88" text-anchor="middle">Call Dean!</text>
  <text class="phone" x="906" y="153" text-anchor="middle">318-555-0187</text>

  <text class="firm-name" x="906" y="242" text-anchor="middle">DEAN MARLOWE</text>
  <text class="firm-tagline" x="906" y="275" text-anchor="middle">ACCIDENT &amp; INJURY LAWYERS</text>
</svg>
</body>
</html>
```